Create a Poster Campaign for a Zurich-based Crowdfinancing Startup

Company: Brightmoor Kapital GmbH (bmk-lend.ch)
Campaign: First major marketing push
Scope: Billboard posters

Company description:
Brightmoor Kapital GmbH is a crowdfinancing platform, where people and businesses needing money can raise funds in three different ways: 1. Crowdlending (borrowing and paying interest), 2. Crowdfactoring for businesses (pre-financing an open invoice), 3. Crowdfunding (rewards-based funding). What Brightmoor Kapital from the competitors differentiates is that borrowers can borrow at their own conditions (amount, duration up to 5 years, and interest rate).
MORE INFO: www.bmk-lend.ch

We are also changing website colours to blue away from brown.

Need:
We need to attract more users to the platform and because we only operate in Switzerland, a poster campaign is meant to create awareness of our brand and services.

We need 2 posters designs in F 200 and F 24 Large Format (Here is a tool to see poster sizes (https://booking.velorapost.ch/en/poster-design-tips-and-checklist)

Notes:
We would like to use bmk-lend.ch as the name and address of the platform. We do not want plant motifs (growth of a plant from dirt, or money growing).

Slogan Ideas:
Too much money? Not enough money? Come to BMK.

We’ve got your next loan.

Balanced for borrowers and lenders. <— potentially a secondary text block

Target Market(s)

People who need money (businesses and private people) as well as people and businesses looking to invest money. It needs to speak to both.

Industry/Entity Type

Financial

Font styles to use
Serif
Sans Serif

Colors
0355a3
3276b5
85acd3
cedeed

Requirements
Must have
• Message and headline: must get across in 1–2 seconds, be catchy and easy to grasp
• Few words: maximum of ten
• Font size should make text readable up to ten metres
• High contrast dark on light and complementary colours are easiest to take in
• Logo must be clearly recognizable.
• Elements essential to the image, such as texts, should be placed at least 6 cm – in the case of F12 and F24 – and 4 cm – in the case of F4 and F200 formats – from the edge at the top, bottom and sides (this is mandatory in the case of posters placed in light boxes).
Nice to have
• Kelvo and Lendra Square have done some creative posters.
Should not have
• No plant images

```html
<!DOCTYPE html>
<html lang="en">
<head>
<meta charset="utf-8">
<title>Brightmoor Kapital – Poster</title>
<link rel="stylesheet" href="https://fonts.googleapis.com/css2?family=Oswald:wght@500;600;700&family=Open+Sans:wght@400;600&display=swap">
<style>
  :root {
    --navy: #0a4a8c;
    --navy-deep: #083f7a;
    --blue-glow: #1d76c6;
    --cyan: #1ccdf6;
    --white: #ffffff;
    --skin: #c9a27c;
    --shirt: #b48a5e;
  }
  * { margin: 0; padding: 0; box-sizing: border-box; }
  html, body { width: 869px; height: 1200px; overflow: hidden; background: var(--white); }
  .poster {
    position: relative;
    width: 869px;
    height: 1200px;
    overflow: hidden;
    background: radial-gradient(ellipse 65% 45% at 50% 52%, var(--blue-glow) 0%, var(--navy) 70%, var(--navy-deep) 100%);
    font-family: "Open Sans", Arial, sans-serif;
  }
  .backdrop { position: absolute; inset: 0; width: 869px; height: 1200px; }
  .brand {
    position: absolute; top: 42px; left: 0; right: 0;
    display: flex; justify-content: center; align-items: center; gap: 12px;
  }
  .brand-dot { width: 40px; height: 40px; border-radius: 50%; background: var(--white); }
  .brand-name {
    font-family: "Oswald", Arial, sans-serif; font-weight: 600;
    font-size: 28px; color: var(--white); letter-spacing: 0.5px;
  }
  .headline {
    position: absolute; font-family: "Oswald", Arial, sans-serif; font-weight: 700;
    color: var(--cyan); font-size: 64px; line-height: 1; white-space: nowrap;
  }
  .headline--first { top: 122px; left: 83px; }
  .headline--second { top: 188px; left: 279px; }
  .call {
    position: absolute; top: 258px; left: 0; right: 0; text-align: center;
    font-family: "Oswald", Arial, sans-serif; font-weight: 700;
    font-size: 108px; line-height: 1.05; color: var(--white);
  }
  .tagline {
    position: absolute; top: 372px; left: 0; right: 0; text-align: center;
    font-weight: 600; font-size: 29px; color: var(--white);
  }
  .photo {
    position: absolute; left: 97px; top: 420px; width: 590px; height: 482px;
    border-radius: 45% 45% 0 0 / 30% 30% 0 0;
    background: linear-gradient(180deg, rgba(201,162,124,0.55) 0%, var(--shirt) 45%, #8f6a45 100%);
  }
  .steps { position: absolute; top: 935px; left: 0; width: 869px; height: 180px; }
  .steps-line {
    position: absolute; top: 83px; left: 165px; width: 541px; height: 5px; background: var(--cyan);
  }
  .step {
    position: absolute; top: 0; width: 170px; height: 176px; margin-left: -85px;
  }
  .step:nth-of-type(2) { left: 165px; }
  .step:nth-of-type(3) { left: 434px; }
  .step:nth-of-type(4) { left: 706px; }
  .step-disc {
    position: absolute; top: 6px; left: 0; width: 170px; height: 170px; border-radius: 50%;
    background: var(--navy); border: 6px solid var(--cyan);
    display: flex; flex-direction: column; align-items: center; justify-content: center;
    text-align: center; color: var(--white); padding: 10px 14px 0;
  }
  .step-num {
    position: absolute; top: -14px; left: 60px; width: 50px; height: 50px; border-radius: 50%;
    background: var(--cyan); border: 4px solid var(--white); z-index: 2;
    font-family: "Oswald", Arial, sans-serif; font-weight: 600; font-size: 30px;
    color: var(--white); display: flex; align-items: center; justify-content: center;
  }
  .step-title { font-family: "Oswald", Arial, sans-serif; font-weight: 600; font-size: 23px; line-height: 1.15; }
  .step-text { font-size: 15px; line-height: 1.3; }
  .footer-text {
    position: absolute; top: 1145px; left: 0; right: 0; text-align: center;
    font-weight: 600; font-size: 28px; color: var(--cyan);
  }
</style>
</head>
<body>
<main class="poster">
  <svg class="backdrop" viewBox="0 0 869 1200" aria-hidden="true">
    <path d="M0 745 Q434 1010 869 755 L869 778 Q434 1012 0 770 Z" fill="var(--cyan)"/>
    <path d="M0 770 Q434 1012 869 778 L869 1200 L0 1200 Z" fill="var(--white)"/>
    <path d="M0 1150 Q434 1095 869 1150 L869 1200 L0 1200 Z" fill="var(--navy)"/>
  </svg>

  <header class="brand">
    <span class="brand-dot"></span>
    <span class="brand-name">Brightmoor Kapital</span>
  </header>

  <h1 class="headline headline--first">Too much MONEY?</h1>
  <h1 class="headline headline--second">Not enough MONEY?</h1>
  <p class="call">Come to BMK</p>
  <p class="tagline">Balanced for borrowers and lenders</p>

  <div class="photo" role="img" aria-label="Photo of a puzzled man in glasses and tie shrugging, holding banknotes in one hand"></div>

  <section class="steps">
    <div class="steps-line"></div>
    <div class="step">
      <span class="step-num">1</span>
      <div class="step-disc">
        <span class="step-title">Crowdlending</span>
        <span class="step-text">(borrowing and paying interest),</span>
      </div>
    </div>
    <div class="step">
      <span class="step-num">2</span>
      <div class="step-disc">
        <span class="step-title">Crowdfactoring</span>
        <span class="step-text">for businesses (pre-financing an open invoice),</span>
      </div>
    </div>
    <div class="step">
      <span class="step-num">3</span>
      <div class="step-disc">
        <span class="step-title">Crowdfunding</span>
        <span class="step-text">(rewards-based funding).</span>
      </div>
    </div>
  </section>

  <p class="footer-text">more visit&nbsp; at : www.bmk-lend.ch</p>
</main>
</body>
</html>
```